Dunmore Roofing

Want a professional looking business card

Industry/Entity Type

Business

Contact Information for Business Card

Paul Dunmore ( Owner) paul@dunmoreroofing-example.com, www.dunmoreroofing-example.com, Adress: 4172 Township road 43 Brookvale,ON K9X4T2

```html
<!DOCTYPE html>
<html lang="en">
<head>
<meta charset="utf-8">
<title>Dunmore Roofing – Business Card</title>
<link rel="stylesheet" href="https://fonts.googleapis.com/css2?family=Exo+2:wght@700&family=PT+Sans:wght@400&display=swap">
<style>
  :root {
    --stage: #1b1b1b;
    --card-light: #f2f2f2;
    --brand-blue: #1c4582;
    --pattern-blue: #2a5390;
    --ink: #2a2a2a;
    --white: #ffffff;
  }
  * { margin: 0; padding: 0; box-sizing: border-box; }
  html, body {
    width: 1200px;
    height: 900px;
    overflow: hidden;
    background: var(--stage);
  }
  .stage {
    position: relative;
    width: 1200px;
    height: 900px;
  }
  .card {
    position: absolute;
    top: 170px;
    width: 347px;
    height: 561px;
  }
  .card--front {
    left: 259px;
    background: var(--card-light);
    text-align: center;
    font-family: "PT Sans", sans-serif;
    color: var(--ink);
  }
  .card--back {
    left: 631px;
    background: var(--brand-blue);
    overflow: hidden;
  }
  .brand-name {
    position: absolute;
    left: 0;
    right: 0;
    top: 92px;
    font-family: "Exo 2", sans-serif;
    font-weight: 700;
    color: var(--brand-blue);
    font-size: 44px;
    line-height: 1.05;
    letter-spacing: 1px;
    text-transform: uppercase;
  }
  .contact {
    position: absolute;
    left: 0;
    right: 0;
    top: 349px;
  }
  .contact__name {
    font-family: "Exo 2", sans-serif;
    font-weight: 700;
    font-size: 23px;
    line-height: 1;
    color: var(--brand-blue);
    text-transform: uppercase;
  }
  .contact__role {
    font-size: 15px;
    line-height: 1;
    margin-top: 5px;
  }
  .contact__rule {
    width: 147px;
    height: 1px;
    background: var(--brand-blue);
    margin: 15px auto 17px;
  }
  .contact__line {
    font-size: 16px;
    line-height: 20px;
  }
  .contact__gap { height: 9px; }
  .back-pattern {
    position: absolute;
    inset: 0;
    background: linear-gradient(180deg, var(--pattern-blue), var(--brand-blue) 50%, var(--pattern-blue));
    opacity: 0.55;
  }
  .back-mark {
    position: absolute;
    left: 0;
    right: 0;
    top: 424px;
    text-align: center;
    font-family: "Exo 2", sans-serif;
    font-weight: 700;
    font-size: 30px;
    line-height: 1;
    color: var(--white);
    text-transform: uppercase;
    letter-spacing: 1px;
  }
</style>
</head>
<body>
  <main class="stage">
    <section class="card card--front">
      <div class="brand-name">Dunmore<br>Roofing</div>
      <div class="contact">
        <div class="contact__name">Paul Dunmore</div>
        <div class="contact__role">Owner</div>
        <div class="contact__rule"></div>
        <div class="contact__line">4172 Township road 43</div>
        <div class="contact__line">Brookvale,ON K9X4T2</div>
        <div class="contact__gap"></div>
        <div class="contact__line">paul@dunmoreroofing-example.com</div>
        <div class="contact__line">www.dunmoreroofing-example.com</div>
      </div>
    </section>
    <section class="card card--back">
      <div class="back-pattern" role="img" aria-label="Faint repeating brand monogram pattern across the card back"></div>
      <div class="back-mark">Dunmore</div>
    </section>
  </main>
</body>
</html>
```